lantern pathway for children needs a website designer

We need a website designer for our new extension to our company known as 'lantern pathway' providing shadow support services to children based in Singapore. We are a sister branch of a private clinic 'Bright horizons' providing speech language, occupational, and educational therapy to children.

We would like to use our own photos. So the selected design should have a frame with pictures to give us an idea but we will replace them with our own. We will be needing help with inputting information and changing information throughout.

We would like to see designs that are simple, and professional. We have a logo (see attached). The result should convey professionalism in shadow support, fostering independent thinking and moving students towards self-learning.

Target Market(s)

Teachers, psychologists, parents

Industry/Entity Type

Clinic

Requirements
Should not have
• too distracting colours

```html
<!DOCTYPE html>
<html lang="en">
<head>
<meta charset="utf-8">
<title>Lantern Pathway – Shadow Support</title>
<link rel="stylesheet" href="https://fonts.googleapis.com/css2?family=Open+Sans:wght@300;400;600;700&display=swap">
<style>
  :root {
    --maroon-deep: #760304;
    --maroon-nav: #8a0b0b;
    --hero: #8b3b3b;
    --section-red: #7a2626;
    --footer-red: #7b2222;
    --text-red: #8a1414;
    --paper: #f2f2f2;
    --mist: #e1e1e1;
    --grey-text: #7a7a7a;
    --dark-text: #444;
    --orange: #f7941d;
    --white: #fff;
  }
  * { box-sizing: border-box; margin: 0; padding: 0; }
  html, body { width: 1200px; height: 2177px; overflow: hidden; }
  body {
    position: relative;
    font-family: "Open Sans", Arial, sans-serif;
    background: var(--mist);
    color: var(--dark-text);
  }
  .abs { position: absolute; }
  a { color: inherit; text-decoration: none; }

  /* top bar */
  .top-bar { left: 0; top: 0; width: 1200px; height: 25px; background: var(--maroon-deep); }
  .login-link { right: 64px; top: 4px; color: var(--white); font-size: 13px; letter-spacing: .2px; }

  /* header */
  .header { left: 0; top: 25px; width: 1200px; height: 436px; background: var(--paper); }
  .brand { left: 58px; top: 76px; font-size: 30px; font-weight: 700; color: var(--maroon-nav); letter-spacing: -.3px; }
  .social { display: flex; gap: 11px; }
  .social span { width: 26px; height: 26px; border-radius: 50%; display: block; }
  .social .s1 { background: #55acee; }
  .social .s2 { background: #3b5998; }
  .social .s3 { background: #00a3e0; }
  .social .s4 { background: #f7921e; }
  .header-social { left: 1001px; top: 58px; }
  .search { left: 943px; top: 97px; width: 197px; height: 37px; display: flex; }
  .search-field { flex: 1; border: 1px solid #d8a0a0; background: var(--white); font-size: 13px; color: #aaa; padding: 9px 12px; }
  .search-btn { width: 44px; background: var(--maroon-nav); display: flex; align-items: center; justify-content: center; }

  /* navigation */
  .main-nav { left: 46px; top: 160px; width: 1108px; height: 48px; background: var(--maroon-nav); display: flex; align-items: center; }
  .main-nav a { color: var(--white); font-size: 16.5px; padding: 0 0 0 39px; }
  .main-nav a:nth-child(2) { padding-left: 60px; }
  .main-nav a:nth-child(3), .main-nav a:nth-child(4), .main-nav a:nth-child(5), .main-nav a:nth-child(6) { padding-left: 51px; }
  .main-nav .nav-register { position: absolute; left: 864px; top: 0; height: 48px; width: 164px; background: #000; padding: 0; display: flex; align-items: center; justify-content: center; }

  /* hero */
  .hero { left: 46px; top: 208px; width: 1108px; height: 319px; background: var(--hero); overflow: hidden; }
  .hero-photo { position: absolute; left: 77px; top: -66px; width: 500px; height: 500px; border-radius: 50%; border: 12px solid var(--white); background: radial-gradient(circle at 45% 55%, #c9a98a, #8a6a58 60%, #5a4238); }
  .hero-kicker { left: 813px; top: 232px; color: var(--white); font-size: 21px; font-weight: 300; }
  .hero-title { left: 694px; top: 254px; color: var(--white); font-size: 36px; font-weight: 300; letter-spacing: .5px; }
  .hero-text { left: 695px; top: 303px; width: 390px; color: var(--white); font-size: 13.8px; line-height: 25.5px; }
  .hero-btn { left: 695px; top: 441px; width: 186px; height: 36px; background: var(--maroon-deep); color: var(--white); font-size: 14.5px; display: flex; align-items: center; justify-content: center; }
  .hero-dots { left: 986px; top: 495px; display: flex; gap: 4px; }
  .hero-dots span { width: 14px; height: 14px; border-radius: 50%; background: #d8c8c8; }
  .hero-dots span.on { background: var(--white); }

  /* feature cards */
  .card { top: 592px; width: 282px; }
  .card-photo { height: 180px; border-top: 7px solid var(--maroon-nav); }
  .card-text { margin-top: 20px; height: 62px; overflow: hidden; font-size: 15px; line-height: 21px; color: var(--text-red); text-align: justify; padding: 0 2px; }
  .card-more { font-size: 15px; color: var(--grey-text); margin-top: -2px; }

  /* shadow support */
  .support { left: 0; top: 926px; width: 1200px; height: 479px; background: var(--section-red); color: var(--white); text-align: center; }
  .support-title { position: absolute; left: 0; width: 1200px; top: 31px; font-size: 21px; letter-spacing: .5px; }
  .support-text { position: absolute; left: 0; width: 1200px; top: 86px; font-size: 15.5px; line-height: 24px; color: #f2dede; }
  .need { position: absolute; top: 195px; width: 240px; }
  .need-circle { width: 144px; height: 144px; margin: 0 auto; border-radius: 50%; background: var(--white); display: flex; align-items: center; justify-content: center; }
  .need-art { width: 78px; height: 78px; border-radius: 50%; background: #f0dcdc; }
  .need-label { margin-top: 14px; font-size: 14px; line-height: 15px; font-family: Arial, sans-serif; }

  /* info */
  .info-heading { font-size: 20px; color: var(--text-red); font-weight: 400; }
  .info-text { font-size: 15px; line-height: 21.5px; color: var(--grey-text); width: 488px; }
  .collab-note { color: var(--grey-text); }
  .collab-sub { left: 655px; top: 1497px; font-size: 15px; color: #666; }
  .collab-list { left: 651px; top: 1534px; width: 486px; list-style: none; }
  .collab-list li { position: relative; padding-left: 18px; font-size: 13px; line-height: 21.5px; color: #777; }
  .collab-list li + li { margin-top: 20px; }
  .collab-list li svg { position: absolute; left: 0; top: 5px; }

  /* footer */
  .footer { left: 0; top: 1844px; width: 1200px; height: 295px; background: var(--footer-red); color: var(--white); }
  .footer-title { position: absolute; top: 33px; font-size: 19px; font-weight: 400; letter-spacing: .3px; }
  .footer-links { position: absolute; top: 82px; list-style: none; font-size: 16px; line-height: 23.5px; }
  .footer-links .active { color: var(--orange); }
  .field { position: absolute; left: 116px; width: 235px; background: var(--white); border-radius: 3px; font-size: 13px; color: #aaa; padding: 6px 10px; }
  .send-btn { position: absolute; left: 116px; top: 247px; width: 235px; height: 33px; background: var(--orange); border-radius: 3px; font-size: 15px; display: flex; align-items: center; justify-content: center; }
  .footer-social { position: absolute; left: 937px; top: 171px; }
  .bottom-bar { left: 0; top: 2139px; width: 1200px; height: 38px; background: var(--maroon-deep); color: var(--white); font-size: 12.5px; text-align: center; line-height: 38px; }
</style>
</head>
<body>

<div class="abs top-bar"></div>
<a class="abs login-link" href="#">LOGIN ACCOUNT ▼</a>

<header class="abs header"></header>
<div class="abs brand">Lantern Pathway</div>
<div class="abs social header-social"><span class="s1"></span><span class="s2"></span><span class="s3"></span><span class="s4"></span></div>
<div class="abs search">
  <div class="search-field">SEARCH</div>
  <div class="search-btn">
    <svg width="22" height="22" viewBox="0 0 22 22"><circle cx="8.5" cy="8.5" r="6" fill="none" stroke="#fff" stroke-width="2.6"/><line x1="13" y1="13" x2="20" y2="20" stroke="#fff" stroke-width="3.4" stroke-linecap="round"/></svg>
  </div>
</div>

<nav class="abs main-nav">
  <a href="#">Home</a>
  <a href="#">About us</a>
  <a href="#">Our Mission</a>
  <a href="#">Shadow Support</a>
  <a href="#">For Referrers</a>
  <a href="#">Contact us</a>
  <a href="#" class="nav-register">Register as Shadow</a>
</nav>

<section class="abs hero">
  <div class="hero-photo" role="img" aria-label="Photo of a therapist working with a young child at a tablet"></div>
</section>
<div class="abs hero-kicker">WELCOME TO</div>
<h1 class="abs hero-title">LANTERN PATHWAY</h1>
<p class="abs hero-text">Lantern Pathway is part of the Clearwell Communication Group of Companies, who are providing speech language therapy, occupational therapy and educational therapy services to both the Singapore and the international school community.</p>
<a class="abs hero-btn" href="#">LEARN MORE</a>
<div class="abs hero-dots"><span></span><span></span><span></span><span class="on"></span></div>

<article class="abs card" style="left:103px">
  <div class="card-photo" role="img" aria-label="Photo of children learning on a classroom mat with a shadow" style="background:linear-gradient(135deg,#3d5aa8,#c9a34a 55%,#7a4a3a)"></div>
  <p class="card-text">Train shadows with a strong focus on equipping them with dynamic, clinical skills.</p>
  <div class="card-more">Read more &gt;</div>
</article>
<article class="abs card" style="left:451px">
  <div class="card-photo" role="img" aria-label="Photo of a professional mentoring a shadow at a computer" style="background:linear-gradient(135deg,#4a4038,#b8a890 50%,#6a5a50)"></div>
  <p class="card-text">Provide families with well-trained Shadows who are mentored by Speech Language Pathologists and Professional</p>
  <div class="card-more">Read more &gt;</div>
</article>
<article class="abs card" style="left:805px">
  <div class="card-photo" role="img" aria-label="Group photo of the educational professionals team" style="background:linear-gradient(180deg,#d8d4d0,#8a8480 60%,#3a3634)"></div>
  <p class="card-text">Work with educational professionals (Educational Psychologists) to provide an effective solution to the learning</p>
  <div class="card-more">Read more &gt;</div>
</article>

<section class="abs support">
  <h2 class="support-title" style="font-weight:400">SHADOW SUPPORT</h2>
  <p class="support-text">A shadow support is para-professional who can help a struggling student to integrate and learn in their school environment.<br>At different points in a student’s life, there may be a need for a para-professional who could step in to help make a difference.<br>Students who need shadows are those who</p>
  <div class="need" style="left:204px">
    <div class="need-circle"><div class="need-art" role="img" aria-label="Icon of a student sitting at a desk"></div></div>
    <p class="need-label">Have difficulties in integrating<br>learning in classroom</p>
  </div>
  <div class="need" style="left:484px">
    <div class="need-circle"><div class="need-art" role="img" aria-label="Icon showing social difficulty"></div></div>
    <p class="need-label">Have social challenges and find it<br>difficult to connect with peers</p>
  </div>
  <div class="need" style="left:774px">
    <div class="need-circle"><div class="need-art" role="img" aria-label="Icon of a student reading a book"></div></div>
    <p class="need-label">Have difficulties in understanding<br>instructions</p>
  </div>
</section>

<h3 class="abs info-heading" style="left:59px;top:1455px">What are its Advantages?</h3>
<p class="abs info-text" style="left:61px;top:1496px">A fully trained shadow support is an asset to the student who other-wise would have trouble fitting in and adapting to the mainstream school environment.</p>
<p class="abs info-text" style="left:61px;top:1580px">Additionally, working closely with the therapist at the centre would mean that the shadow is equipped with the skills necessary to not just adapt, but truly learn.</p>
<h3 class="abs info-heading" style="left:58px;top:1678px">How do I know if my child needs shadowing</h3>
<p class="abs info-text" style="left:61px;top:1717px">A consultation with our Speech Language Pathologist, along with an assessment by an Educational Psychologist would provide us with an indication of whether the child requires shadowing.</p>

<h3 class="abs info-heading" style="left:651px;top:1456px">How You Can Collaborate With Us <span class="collab-note">(For Referrers)</span></h3>
<div class="abs collab-sub">How You Can Collaborate With Us</div>
<ul class="abs collab-list">
  <li><svg width="10" height="12" viewBox="0 0 10 12"><path d="M2 1l6 5-6 5" fill="none" stroke="#8a0b0b" stroke-width="2.5"/></svg>Shadow Supportwill participate in a collaborative working relationship with the professionals working with each student to facilitate progress</li>
  <li><svg width="10" height="12" viewBox="0 0 10 12"><path d="M2 1l6 5-6 5" fill="none" stroke="#8a0b0b" stroke-width="2.5"/></svg>Goals set out by professionals will be supported by the Shadow Support</li>
  <li><svg width="10" height="12" viewBox="0 0 10 12"><path d="M2 1l6 5-6 5" fill="none" stroke="#8a0b0b" stroke-width="2.5"/></svg>Frequent feedback and updates will be provided by the Shadow Support so that goals can remain relevant and up to date</li>
</ul>

<footer class="abs footer">
  <h4 class="footer-title" style="left:116px">QUICK ENQUIRY</h4>
  <div class="field" style="top:74px;height:32px">Name</div>
  <div class="field" style="top:115px;height:31px">Email</div>
  <div class="field" style="top:154px;height:84px">Message</div>
  <div class="send-btn">SEND MESSAGE</div>

  <h4 class="footer-title" style="left:425px">F.A.Q</h4>
  <ul class="footer-links" style="left:425px;top:88px;line-height:27.5px">
    <li class="active">&gt; For Parents</li>
    <li>&gt; For Referrers</li>
    <li>&gt; For Schools</li>
  </ul>

  <h4 class="footer-title" style="left:667px">NAVIGATION</h4>
  <ul class="footer-links" style="left:670px">
    <li>&gt; Home</li>
    <li>&gt; About us</li>
    <li>&gt; Our Mission</li>
    <li>&gt; Shadow Support</li>
    <li>&gt; Contact us</li>
  </ul>

  <h4 class="footer-title" style="left:929px">USEFUL LINKS</h4>
  <ul class="footer-links" style="left:931px;line-height:26.5px">
    <li>&gt; SITEMAP</li>
    <li>&gt; PRIVACY POLICY</li>
    <li>&gt; TERMS &amp; USAGE</li>
  </ul>
  <div class="social footer-social"><span class="s1"></span><span class="s2"></span><span class="s3"></span><span class="s4"></span></div>
</footer>
<div class="abs bottom-bar">Copyright © 2013. Lantern Pathway All Rights Reserved.</div>

</body>
</html>
```